I have a logo and need to design the business card and stationery.
Updates

The uploaded logo image named as GREYMARSH CONSTRUCTION which is to be replaced to GREYMARSH CONTRACTS. Kindly add below details and submit the designs- Company name- Greymarsh Engineering Contracts LLP Name & Post- Kelvan Joshi (Designated Partner) Address- Block No.317, Wing C, Tulvo Trade Court, Manek Pural Road, Ruparel Industrial Estate, Goregaon(E), Mumbai - 400 063 Contact- +91 97415 60382 Email- kelvanjoshi@mailbrook.example Website- www.greymarshcontracts.example Contact for Letterhead- +91-22-28754193

Hi Tovin Rahul, We are liking your Design #28860835. We have suggested some changes which are mentioned in feedback. Kindly revert with it asap to finalize this design.

Colors

Designer to choose colors to be used in the design.

```html
<!DOCTYPE html>
<html lang="en">
<head>
<meta charset="utf-8">
<title>Greymarsh Contracts – Business Card</title>
<link href="https://fonts.googleapis.com/css2?family=Montserrat:wght@700&family=Roboto:wght@400&display=swap" rel="stylesheet">
<style>
  :root {
    --backdrop: #d9d9d9;
    --card-dark: #262626;
    --card-light: #ffffff;
    --silver: #b9b9b9;
    --ink: #2a2a2a;
    --ink-soft: #5a5a5a;
    --rule: #3a3a3a;
  }
  * { box-sizing: border-box; margin: 0; padding: 0; }
  html, body { width: 1200px; height: 1129px; overflow: hidden; }
  body {
    background: var(--backdrop);
    font-family: "Roboto", Arial, sans-serif;
    position: relative;
  }
  .card {
    position: absolute;
    left: 180px;
    width: 840px;
    height: 480px;
    box-shadow: 0 10px 30px rgba(0,0,0,.25);
  }
  .card--front { top: 60px; background: var(--card-dark); }
  .card--back  { top: 589px; background: var(--card-light); }

  .brand {
    display: flex;
    flex-direction: column;
    align-items: center;
    gap: 22px;
    font-family: "Montserrat", Arial, sans-serif;
    font-weight: 700;
    letter-spacing: 2px;
    text-align: center;
  }
  .brand__square { width: 110px; height: 110px; border: 14px solid currentColor; }
  .brand__name { font-size: 40px; line-height: 1.15; }
  .card--front .brand {
    color: var(--silver);
    position: absolute; left: 50%; top: 50%;
    transform: translate(-50%, -50%);
  }
  .card--back .brand {
    color: var(--ink);
    position: absolute; left: 40px; top: 50%;
    width: 340px;
    transform: translateY(-50%);
  }
  .card--back .brand__square { width: 90px; height: 90px; border-width: 12px; }
  .card--back .brand__name { font-size: 31px; }

  .divider {
    position: absolute; left: 410px; top: 90px;
    width: 2px; height: 300px; background: var(--rule);
  }
  .contact {
    position: absolute; left: 440px; top: 78px;
    width: 380px;
    color: var(--ink-soft);
    font-size: 17px; line-height: 1.4;
  }
  .contact__name {
    font-family: "Montserrat", Arial, sans-serif;
    font-weight: 700; font-size: 23px; letter-spacing: 1px;
    color: var(--ink);
  }
  .contact__role { margin-bottom: 12px; }
  .contact__address { margin-bottom: 6px; padding-left: 16px; }
  .contact__row { display: flex; align-items: center; gap: 8px; }
  .contact__row--plain { padding-left: 26px; }
  .contact__row svg { width: 18px; height: 18px; flex: none; fill: none; stroke: var(--ink); stroke-width: 1.8; }
</style>
</head>
<body>
  <section class="card card--front">
    <div class="brand">
      <div class="brand__square"></div>
      <div class="brand__name">GREYMARSH<br>CONTRACTS</div>
    </div>
  </section>

  <section class="card card--back">
    <div class="brand">
      <div class="brand__square"></div>
      <div class="brand__name">GREYMARSH<br>CONTRACTS</div>
    </div>
    <div class="divider"></div>
    <div class="contact">
      <p class="contact__name">KELVAN JOSHI</p>
      <p class="contact__role">Designated Partner</p>
      <p class="contact__address">Block No.317, Wing C,<br>Tulvo Trade Court, Manek Pural Road,<br>Ruparel Industrial Estate,<br>Goregaon(E), Mumbai - 400 063</p>
      <p class="contact__row contact__row--plain">+91 97415 60382</p>
      <p class="contact__row">
        <svg viewBox="0 0 20 20"><rect x="5" y="1.5" width="10" height="17" rx="2"/><line x1="8.5" y1="15.5" x2="11.5" y2="15.5"/></svg>
        +91 97415 60382
      </p>
      <p class="contact__row">
        <svg viewBox="0 0 20 20"><path d="M2 8 Q10 2 18 8 L15 9 L13 7 H7 L5 9 Z"/><rect x="4" y="10" width="12" height="7" rx="1"/></svg>
        +91-22-28754193
      </p>
      <p class="contact__row">
        <svg viewBox="0 0 20 20"><rect x="2" y="4.5" width="16" height="11"/><polyline points="2,4.5 10,11 18,4.5"/></svg>
        kelvanjoshi@mailbrook.example
      </p>
      <p class="contact__row">
        <svg viewBox="0 0 20 20"><circle cx="10" cy="10" r="8"/><ellipse cx="10" cy="10" rx="3.5" ry="8"/><line x1="2" y1="10" x2="18" y2="10"/></svg>
        www.greymarshcontracts.example
      </p>
    </div>
  </section>
</body>
</html>
```